Business card for denture clinic Veltrimora

We need a new business card with our new logo. We are a denture clinic in New Zealand with our target market being 45+ years old. We would need a space on the back to write our patients next appointment on. We would space for only one appointment rather than a list. We will attach a photo showing an example of this. But of course, we would like to see your twist on this. We want it to be bold and easy to read and a good mixture of professional but modern. We have attached our logo to be used on the card.

Target Market(s)

People aged 45+ needing dentures

Industry/Entity Type

Dental

Contact Information for Business Card

We want our logo on the front and the space to write an appointment on the back. I've attached an example our our old business card showing this. We need to have the technicians details on the front.

Font styles to use
Sans Serif

Colors
0255a3
919191
fbfbfb

Requirements
Must have
• The following details:
• Liam Dorsett BDT, PGDipCDentTech Calverin
• Dental Prosthetist
• Phone numbers: 0800 47 3125
• 09 572 1394
• Email: liam@veltrimora.co.nz
• www.veltrimora.co.nz
• Address: 14 Marlow Crest Road
• Halbrook West
• Auckland 0793
Nice to have
• We would like our business cards to have more than just two colours as we want them to be more vibrant. We have uploaded an example of a business card we liked that showed this.

```html
<!DOCTYPE html>
<html lang="en">
<head>
<meta charset="utf-8">
<title>Veltrimora – Business Card</title>
<link rel="stylesheet" href="https://fonts.googleapis.com/css2?family=Ubuntu:ital,wght@0,400;0,500;0,700;1,400&display=swap">
<style>
  :root {
    --brand-blue: #0670ba;
    --brand-grey: #7a7476;
    --card-white: #ffffff;
    --field-white: #f4f4f4;
    --page-bg: #ece8e2;
  }
  * { margin: 0; padding: 0; box-sizing: border-box; }
  html, body {
    width: 1200px; height: 987px; overflow: hidden;
    background: var(--page-bg);
    font-family: "Ubuntu", sans-serif;
  }
  .stage {
    position: relative;
    width: 1024px; height: 842px;
    transform: scale(1.171875);
    transform-origin: top left;
  }
  .card {
    position: absolute;
    left: 250px;
    width: 525px; height: 300px;
    border-radius: 16px;
    overflow: hidden;
    box-shadow: 0 2px 6px rgba(0,0,0,0.18);
  }
  .card--front { top: 111px; background: var(--card-white); }
  .card--back { top: 431px; background: var(--brand-blue); }
  .card__shapes { position: absolute; inset: 0; width: 100%; height: 100%; }

  .brand {
    position: absolute; left: 0; right: 0;
    text-align: center;
  }
  .brand__mark {
    display: block; margin: 0 auto;
    width: 50px; height: 50px; border-radius: 3px;
  }
  .brand__name {
    display: block; margin-top: 9px;
    font-size: 23px; font-weight: 500; letter-spacing: 1px;
    line-height: 1;
  }
  .card--front .brand { top: 36px; }
  .card--front .brand__mark { background: var(--brand-blue); }
  .card--front .brand__name { color: var(--brand-blue); }
  .card--back .brand { top: 48px; }
  .card--back .brand__mark { background: var(--card-white); }
  .card--back .brand__name { color: var(--card-white); }

  .technician {
    position: absolute; left: 0; right: 0; top: 185px;
    text-align: center; color: var(--card-white);
  }
  .technician__name { font-size: 18px; font-weight: 500; }
  .technician__credentials { font-size: 14px; font-weight: 500; }
  .technician__role {
    display: flex; align-items: center; gap: 8px;
    margin: 2px 23px 0;
    font-size: 14px;
  }
  .technician__role::before, .technician__role::after {
    content: ""; flex: 1; height: 1px; background: var(--card-white);
  }
  .contact {
    position: absolute;
    color: var(--card-white); font-size: 13.5px; line-height: 18px;
    font-style: normal;
  }
  .contact--address { left: 23px; top: 235px; }
  .contact--direct { right: 23px; top: 230px; text-align: right; line-height: 20px; }
  .contact__label { font-weight: 700; }

  .appointment__title {
    position: absolute; left: 0; right: 0; top: 172px;
    text-align: center; color: var(--card-white);
    font-size: 19px; font-weight: 500;
  }
  .appointment__field {
    position: absolute; top: 233px;
    width: 205px; height: 37px; border-radius: 19px;
    background: var(--field-white);
    color: var(--brand-blue); font-style: italic; font-size: 15px;
    padding: 9px 14px;
  }
  .appointment__field--date { left: 25px; }
  .appointment__field--time { left: 294px; }
</style>
</head>
<body>
<div class="stage">

  <section class="card card--front" aria-label="Business card front">
    <svg class="card__shapes" viewBox="0 0 525 300" preserveAspectRatio="none" aria-hidden="true">
      <path d="M0,140 C90,156 190,164 265,154 C190,166 90,166 0,156 Z" fill="var(--brand-grey)"/>
      <path d="M0,158 C110,172 240,170 330,160 C420,151 480,160 525,182 L525,300 L0,300 Z" fill="var(--brand-blue)"/>
      <path d="M270,166 C350,152 430,148 492,162 C430,156 350,158 270,166 Z" fill="var(--brand-blue)"/>
    </svg>
    <div class="brand">
      <span class="brand__mark"></span>
      <span class="brand__name">VELTRIMORA</span>
    </div>
    <div class="technician">
      <p><span class="technician__name">LIAM DORSETT</span> <span class="technician__credentials">BDT, PGDipCDentTech Calverin</span></p>
      <p class="technician__role">Dental Prosthetist</p>
    </div>
    <address class="contact contact--address">
      14 Marlow Crest Road<br>
      Halbrook West, Auckland 0793<br>
      www.veltrimora.co.nz
    </address>
    <div class="contact contact--direct">
      <span class="contact__label">P</span> : 0800 47 3125<br>
      <span class="contact__label">C</span> : 09 572 1394<br>
      liam@veltrimora.co.nz
    </div>
  </section>

  <section class="card card--back" aria-label="Business card back">
    <div class="brand">
      <span class="brand__mark"></span>
      <span class="brand__name">VELTRIMORA</span>
    </div>
    <h2 class="appointment__title">Next Appointment</h2>
    <div class="appointment__field appointment__field--date">date:</div>
    <div class="appointment__field appointment__field--time">time:</div>
  </section>

</div>
</body>
</html>
```